Manifesto

I want a manifesto with the following five manifestos for our Not for Profit

- We are a For-purpose organisation
- Every service we offer is free
- Every product we sell funds our services
- Every financial transaction is transparent
- Our service is for the greater good
- Our purpose is always to serve the people
- We are a for purpose organisation

Its to go with this website logo/look/feel www.brightharbour.co.nz

Two attachments:

1. I quite like this look/feel of a manifesto (see attached), I want something clean, professional but I also quite like either Retro modern look feel also like a fresh, and uplifting as its for sick people coming to see us and our funds where anyone buys a product are used for helping those who are sick with healing......so needs something conveyed that is fresh, uplifing yet professional.
2. This attachment is how I wrote this down when inspired of how I wanted Bright Harbour to operate. This is our values chart. It has to say

Also check out our website for our logo, look etc.. it doesnt have to be the same but red somewhere would link back to logo. www.brightharbour.co.nz .

Industry/Entity Type

Financial

```html
<!DOCTYPE html>
<html lang="en">
<head>
<meta charset="utf-8">
<title>Bright Harbour Manifesto</title>
<link rel="stylesheet" href="https://fonts.googleapis.com/css2?family=Lobster&family=Rokkitt:wght@700;800;900&display=swap">
<style>
  :root {
    --backdrop: #e6e6e6;
    --poster-core: #9c0a1f;
    --poster-edge: #5e0410;
    --ink-dark: #3b060d;
    --ink-light: #ffffff;
    --rule: rgba(40, 0, 6, 0.45);
    --shadow: rgba(30, 0, 4, 0.85);
  }
  html, body {
    margin: 0;
    padding: 0;
    width: 1200px;
    height: 1000px;
    overflow: hidden;
    background: var(--backdrop);
  }
  .manifesto-poster {
    position: absolute;
    left: 277px;
    top: 41px;
    width: 648px;
    height: 916px;
    display: block;
  }
  .slab {
    font-family: "Rokkitt", "Rockwell", serif;
    font-weight: 900;
  }
  .script {
    font-family: "Lobster", cursive;
    font-weight: 400;
  }
  .ink-dark { fill: var(--ink-dark); }
  .ink-light {
    fill: var(--ink-light);
    filter: drop-shadow(2px 3px 0 var(--shadow));
  }
  .divider { stroke: var(--rule); stroke-width: 1; }
</style>
</head>
<body>
<svg class="manifesto-poster" viewBox="0 0 648 916" xmlns="http://www.w3.org/2000/svg" role="img" aria-label="Bright Harbour manifesto poster">
  <defs>
    <radialGradient id="poster-glow" cx="50%" cy="50%" r="70%">
      <stop offset="0%" stop-color="var(--poster-core)"/>
      <stop offset="70%" stop-color="#8c0819"/>
      <stop offset="100%" stop-color="var(--poster-edge)"/>
    </radialGradient>
  </defs>
  <rect class="poster-ground" width="648" height="916" fill="url(#poster-glow)"/>

  <!-- heading -->
  <text class="slab ink-dark" x="28" y="105" font-size="122" textLength="592" lengthAdjust="spacingAndGlyphs">WE ARE A</text>
  <text class="slab ink-light" x="24" y="147" font-size="36" textLength="271" lengthAdjust="spacingAndGlyphs">FOR PURPOSE</text>
  <text class="slab ink-dark" x="24" y="184" font-size="33" textLength="271" lengthAdjust="spacingAndGlyphs">ORGANISATION</text>
  <line class="divider" x1="330" y1="122" x2="330" y2="187"/>
  <text class="script ink-light" x="360" y="149" font-size="30" textLength="183" lengthAdjust="spacingAndGlyphs">Every Service</text>
  <text class="script ink-dark" x="436" y="177" font-size="26" textLength="176" lengthAdjust="spacingAndGlyphs">we offer is free</text>
  <line class="divider" x1="63" y1="204" x2="571" y2="204"/>

  <!-- product -->
  <text class="slab ink-light" x="24" y="270" font-size="66" textLength="598" lengthAdjust="spacingAndGlyphs">EVERY PRODUCT</text>
  <text class="slab ink-dark" x="24" y="317" font-size="42" textLength="598" lengthAdjust="spacing">we sell funds our services</text>
  <line class="divider" x1="63" y1="337" x2="571" y2="337"/>

  <!-- finance -->
  <text class="slab ink-light" x="22" y="394" font-size="46" textLength="600" lengthAdjust="spacing">EVERY FINANCIAL</text>
  <text class="slab ink-dark" x="22" y="425" font-size="29" textLength="600" lengthAdjust="spacing">transaction is transparent</text>
  <line class="divider" x1="63" y1="450" x2="571" y2="450"/>

  <!-- service -->
  <text class="slab ink-dark" x="21" y="521" font-size="62" textLength="607" lengthAdjust="spacing">OUR SERVICE IS</text>
  <text class="script ink-light" x="113" y="571" font-size="50" textLength="408" lengthAdjust="spacingAndGlyphs">for the greater good</text>
  <line class="divider" x1="63" y1="610" x2="571" y2="610"/>

  <!-- purpose -->
  <text class="slab ink-dark" x="22" y="679" font-size="62" textLength="606" lengthAdjust="spacing">OUR PURPOSE IS</text>
  <text class="script ink-light" x="65" y="724" font-size="46" textLength="516" lengthAdjust="spacingAndGlyphs">always to serve the people</text>
  <line class="divider" x1="63" y1="760" x2="571" y2="760"/>

  <!-- closing -->
  <text class="slab ink-dark" x="22" y="816" font-size="48" textLength="606" lengthAdjust="spacing">WE ARE A FOR PURPOSE</text>
  <text class="script ink-light" x="113" y="874" font-size="68" textLength="390" lengthAdjust="spacingAndGlyphs">organisation</text>
</svg>
</body>
</html>
```